Agrarhandel benötigt Homepage
Zielgruppe
Wir sind ein Agrarhandel mit einem Warenumschlagslager im Sinne eines klassischen Einzelhandels und vertreiben Produkte an Landwirte.
Wir vertreiben folgende Hauptproduktgruppen:
Einzelfuttermittel
wie z.B. Sojaexktraktionsschrot. Die einzelnen Produkte könnten z.B. wie die Futtermittel auf folgender Seite dargestellt werden (https://www.kornprobe-beispiel.eu/de/produkt/trelomixan)
Mischfuttermittel
Hier bieten wir unseren Kunden an, individuelles Mischfutter auf Basis unserer Einzelfuttermittel herzustellen.
Weitere Details und weitere Produktbereiche habe ich in einer Powerpoint-Übersicht dargestellt.
Neben diesen Produkten wollen wir uns als Familienunternehmen selbst vorstellen. Zudem betreiben wir in unserer Familie zusätzlich einen Milchviehbetrieb den wir ebenfalls hervorheben möchten, da wir unseren Kunden gegenüber einerseits als Zulieferer aber auch als Kollege auftreten wollen.
Einzelfuttermittel: Hier können wir durch unsere Unabhängigkeit punkten, da wir nicht abhängig von bestimmten Lieferanten sind und dementsprechend unabhängig beraten können. Wir untersuchen im Vergleich zu unseren Wettbewerben die Qualität der Futtermittel bis ins Detail und können daher eine Transparenz bieten, die Konkurrenten in der Regel nicht bieten können. Unser Warenumschlagsplatz mit moderner Technik ermöglicht es uns äußerst kosteneffizient die Waren umschlagen und ausliefern zu können.
Mischfuttermittel: Auf Basis der vorhandenen Einzelfuttermittel stellen wir je nach Kundenwunsch individuelle Mischfutter her. Wir arbeiten mit offenen Deklarationen, sodass unsere Kunden jederzeit nachvollziehen können, ob auch die Einzelfuttermittel verwendet wurden, die sie bestellt haben und keine billigen Ersatzprodukte verwendet wurden.
Zudem sind wir BT und HUPA zertifiziert. Die aktuellen für unser Unternehmen ausgestellten Zertifikate müssen für unsere Kunden als Download zur Verfügung stehen. Statt dem HUPA-Logo bitte das ..
Aufgabenstellung
Wir möchten gerne ein zeitgemäße Homepage, jedoch muss auch berücksichtigt werden, dass unsere Kunden eher konservativ denken.

```html
<!DOCTYPE html>
<html lang="de">
<head>
<meta charset="utf-8">
<title>Kornfeld Landhandel – Agrikultural Service</title>
<link rel="stylesheet" href="https://fonts.googleapis.com/css2?family=Roboto:wght@400;500;700;900&display=swap">
<style>
  :root {
    --yellow: #f3c81c;
    --green: #8dc641;
    --ink: #1e1e1e;
    --muted: #555;
    --white: #ffffff;
    --band: #3b2e24;
    --line: #e4e4e4;
  }
  * { box-sizing: border-box; margin: 0; padding: 0; }
  html, body { width: 1200px; height: 800px; overflow: hidden; background: var(--white); }
  body { font-family: "Roboto", Arial, sans-serif; color: var(--ink); position: relative; }

  .site-header { height: 70px; display: flex; align-items: center; padding: 0 48px; gap: 28px; }
  .brand { display: flex; align-items: center; gap: 10px; font-weight: 700; font-size: 22px; color: var(--ink); }
  .brand-mark { width: 26px; height: 26px; border-radius: 50%; background: var(--green); }
  .main-nav { margin-left: auto; display: flex; gap: 22px; font-size: 13px; font-weight: 700; }
  .main-nav a { color: var(--ink); text-decoration: none; }
  .main-nav a.is-active { border-bottom: 2px solid var(--ink); }
  .header-tools { display: flex; align-items: center; gap: 16px; font-size: 13px; font-weight: 700; }
  .cta-subscribe { background: var(--green); color: var(--white); font-size: 11px; line-height: 1.2; text-align: center; padding: 6px 14px; }

  .hero { height: 125px; padding: 10px 48px 0; display: flex; justify-content: space-between; }
  .hero-greeting { font-size: 12px; color: var(--muted); margin-top: 26px; }
  .hero-title { font-size: 52px; font-weight: 900; line-height: 1.1; }
  .hero-title .accent { color: var(--yellow); }
  .newsletter-note { font-size: 12px; color: var(--muted); width: 330px; margin-top: 20px; }

  .category-strip { display: grid; grid-template-columns: repeat(4, 1fr); height: 205px; }
  .category-tile { position: relative; display: flex; align-items: flex-end; padding: 16px 20px; color: var(--white); font-weight: 700; font-size: 19px; }
  .tile-single { background: linear-gradient(160deg, #8fb3c8, #4f6a80 60%, #6b4a34); }
  .tile-mixed { background: linear-gradient(160deg, #c9b59c, #8f6d4f 60%, #4f3a2a); }
  .tile-film { background: linear-gradient(160deg, #c6d3dc, #6d84a0 55%, #7f7048); }
  .tile-seed { background: linear-gradient(160deg, #4a3a22, #c59325 55%, #e6b94a); }

  .company { display: grid; grid-template-columns: 540px 1fr; gap: 40px; padding: 22px 48px 0; height: 290px; }
  .company-media { position: relative; }
  .media-truck { position: absolute; left: 40px; top: 6px; width: 280px; height: 150px; background: linear-gradient(180deg, #7fb2e0, #a7c39b 60%, #c9a662); }
  .media-field { position: absolute; left: 40px; top: 156px; width: 160px; height: 110px; background: linear-gradient(180deg, #c9a662, #8c7a3e); }
  .media-grain { position: absolute; left: 200px; top: 70px; width: 250px; height: 196px; background: linear-gradient(150deg, #b88a52, #e0b87c 50%, #7a5634); }
  .eyebrow { font-size: 11px; color: var(--muted); }
  .company-title { font-size: 27px; font-weight: 700; line-height: 1.15; margin: 4px 0 10px; }
  .company-text p { font-size: 11.5px; line-height: 1.45; color: #333; margin-bottom: 8px; }
  .check-list { list-style: none; display: flex; gap: 28px; font-size: 12px; margin: 4px 0 12px; }
  .check-list li { display: flex; align-items: center; gap: 6px; }
  .btn-yellow { display: inline-block; background: var(--yellow); color: var(--white); font-size: 12px; font-weight: 500; padding: 9px 22px; }

  .fields { position: absolute; left: 0; top: 690px; width: 1200px; height: 110px; background: linear-gradient(90deg, #2f251d, #5a4333 55%, #7a5a45); padding: 14px 48px; display: grid; grid-template-columns: 230px 250px 1fr; gap: 30px; color: var(--white); }
  .fields-title { font-size: 24px; font-weight: 700; padding-bottom: 8px; border-bottom: 1px solid var(--yellow); align-self: start; }
  .field-tabs { list-style: none; font-size: 12px; }
  .field-tabs li { padding: 4px 10px; border-bottom: 1px solid rgba(255,255,255,.25); }
  .field-tabs li.is-active { background: var(--yellow); color: var(--ink); }
  .field-detail h3 { font-size: 14px; margin-bottom: 4px; }
  .field-detail p { font-size: 11px; margin-bottom: 8px; }
  .field-checks { list-style: none; display: grid; grid-template-columns: repeat(2, 160px); gap: 6px; font-size: 11px; }
  .field-checks li { display: flex; align-items: center; gap: 6px; }
  .box-tick { width: 16px; height: 16px; background: var(--yellow); display: inline-flex; align-items: center; justify-content: center; }

  .quick-dock { position: absolute; right: 0; top: 150px; width: 30px; background: var(--yellow); display: flex; flex-direction: column; }
  .quick-dock span { height: 34px; display: flex; align-items: center; justify-content: center; border-bottom: 1px solid rgba(255,255,255,.5); }
</style>
</head>
<body>
  <header class="site-header">
    <div class="brand"><span class="brand-mark"></span>Kornfeld Landhandel</div>
    <nav class="main-nav">
      <a class="is-active" href="#">Start</a><a href="#">Aktuelles</a><a href="#">Unternehmen</a><a href="#">Sortiment</a><a href="#">Shop</a><a href="#">Kontakt</a>
    </nav>
    <div class="header-tools">
      <svg width="15" height="15" viewBox="0 0 16 16" fill="none" stroke="#1e1e1e" stroke-width="2"><circle cx="6.5" cy="6.5" r="5"/><path d="M10.5 10.5l4 4"/></svg>
      <span>+49 9999 123450</span>
      <span class="cta-subscribe">Jetzt<br>Abonnieren</span>
    </div>
  </header>

  <section class="hero">
    <div>
      <p class="hero-greeting">Herzlich Willkommen bei Kornfeld Landhandel, Ihrem Experten in der Agrarwirtschaft.</p>
      <h1 class="hero-title"><span class="accent">Agrikultural</span> Service</h1>
    </div>
    <p class="newsletter-note">Jetzt neu! Abonnieren Sie unsere Newsletter und profitieren Sie als erster von aktuellen Informationen!</p>
  </section>

  <section class="category-strip">
    <div class="category-tile tile-single" role="img" aria-label="Foto: Mitarbeiter prüft Futter in der Anlage">Einzelfuttermittel</div>
    <div class="category-tile tile-mixed" role="img" aria-label="Foto: Hände halten Mischfutter">Mischfuttermittel</div>
    <div class="category-tile tile-film" role="img" aria-label="Foto: Zwei Männer verlegen Silofolie">Silofolien</div>
    <div class="category-tile tile-seed" role="img" aria-label="Foto: Fallende Maiskörner">Saatgut</div>
  </section>

  <section class="company">
    <div class="company-media">
      <div class="media-truck" role="img" aria-label="Foto: LKW mit Kipperauflieger vor Windrad"></div>
      <div class="media-field" role="img" aria-label="Foto: Getreidefeld von oben"></div>
      <div class="media-grain" role="img" aria-label="Foto: Hand mit Getreidekörnern"></div>
    </div>
    <div class="company-text">
      <p class="eyebrow">Unternehmen</p>
      <h2 class="company-title">Für die Optimalste<br>Aufzucht Ihre Tiere</h2>
      <p>Der Agrarhandelsbetrieb Kornfeld Landhandel besteht bereits seit 19xx in Talberg. Gegründet wurde er durch xxxxx Vater des jetzigen geschäftsführenden Gesellschafters xxxxxxx welcher damals eigenes Futtermittel in der hauseigenen kleinen Mühle hergestellt hat.</p>
      <p>Mit 20 Jahren übernahm Kornfeld Landhandel das Geschäft mit damals 30to Futtermittel pro Tag und erstem eigenen LKW, welchen er selber fuhr. Durch stetige Weiterentwicklung und diverser Übernahmen von Landhandelsbetrieben in der Region Talberg mit Getreideannahme,xxxxxx mit Getreideannahme) ist die Kornfeld Landhandel heute ein verlässlicher Partner für die Landwirtschaft und Futtermittelindustrie.</p>
      <ul class="check-list">
        <li><svg width="12" height="10" viewBox="0 0 12 10"><path d="M1 5l3.5 3.5L11 1" fill="none" stroke="#f3c81c" stroke-width="2"/></svg>Handel</li>
        <li><svg width="12" height="10" viewBox="0 0 12 10"><path d="M1 5l3.5 3.5L11 1" fill="none" stroke="#f3c81c" stroke-width="2"/></svg>Transport</li>
        <li><svg width="12" height="10" viewBox="0 0 12 10"><path d="M1 5l3.5 3.5L11 1" fill="none" stroke="#f3c81c" stroke-width="2"/></svg>Agrarwirtschaft</li>
      </ul>
      <a class="btn-yellow">Ansprechpartner</a>
    </div>
  </section>

  <section class="fields" role="region" aria-label="Tätigkeitsfelder, Hintergrundfoto Kühe im Stall">
    <h2 class="fields-title">Tätigkeitsfelder</h2>
    <ul class="field-tabs">
      <li class="is-active">› Futter</li><li>Getreide</li><li>Saatgut</li><li>Landwirtschaftlicher Bedarf</li>
    </ul>
    <div class="field-detail">
      <h3>Futter</h3>
      <p>Wir bieten Ihnen Futtermittel für sowohl Nutz- als auch Hobbytiere!</p>
      <ul class="field-checks">
        <li><span class="box-tick"><svg width="10" height="8" viewBox="0 0 12 10"><path d="M1 5l3.5 3.5L11 1" fill="none" stroke="#fff" stroke-width="2"/></svg></span>Milchvieh</li>
        <li><span class="box-tick"><svg width="10" height="8" viewBox="0 0 12 10"><path d="M1 5l3.5 3.5L11 1" fill="none" stroke="#fff" stroke-width="2"/></svg></span>Schweine</li>
        <li><span class="box-tick"><svg width="10" height="8" viewBox="0 0 12 10"><path d="M1 5l3.5 3.5L11 1" fill="none" stroke="#fff" stroke-width="2"/></svg></span>Hühner</li>
        <li><span class="box-tick"><svg width="10" height="8" viewBox="0 0 12 10"><path d="M1 5l3.5 3.5L11 1" fill="none" stroke="#fff" stroke-width="2"/></svg></span>Biofutter</li>
      </ul>
    </div>
  </section>

  <aside class="quick-dock">
    <span><svg width="14" height="14" viewBox="0 0 16 16" fill="none" stroke="#fff" stroke-width="1.5"><path d="M1 2h2l2 8h8l2-6H4"/><circle cx="6" cy="13.5" r="1"/><circle cx="12" cy="13.5" r="1"/></svg></span>
    <span><svg width="14" height="14" viewBox="0 0 16 16" fill="none" stroke="#fff" stroke-width="1.5"><rect x="1.5" y="3.5" width="13" height="9"/><path d="M1.5 3.5l6.5 5 6.5-5"/></svg></span>
    <span><svg width="14" height="14" viewBox="0 0 16 16" fill="none" stroke="#fff" stroke-width="1.5"><rect x="1.5" y="2.5" width="13" height="11"/><path d="M1.5 6h13"/></svg></span>
  </aside>
</body>
</html>
```